Blind Rivet Product catalogue

Need a design in wordpress with a productcatalogue where i present all products. This is a B2B business. The products is Blindrivets and Blindrivet nuts and accessories to this. I only want the basic information and also technical specification.

This is a subcompany to my existing company k7.m3.se but specializing in a subcategory

Businesses using blind rivet technology.

Industrial

Sans Serif

Must have
• Three different categories for the products; Blind Rivets - Blind Rivet Nut - Riveting Tools
Nice to have
• Possible to ad login for more information of the different sizes

```html
<!DOCTYPE html>
<html lang="en">
<head>
<meta charset="utf-8">
<title>Blind Rivet – Product Catalogue</title>
<link href="https://fonts.googleapis.com/css2?family=Open+Sans:wght@400;600;700&family=Raleway:wght@300;400;500;600;700&display=swap" rel="stylesheet">
<style>
:root{
  --green:#76bc43;
  --green-dark:#5fa02f;
  --black:#0d0d0d;
  --ink:#222;
  --muted:#666;
  --line:#cfcfcf;
  --soft:#f0f0f0;
  --white:#fff;
}
*{box-sizing:border-box;margin:0;padding:0}
html,body{width:1200px;height:2592px;overflow:hidden}
body{font-family:"Open Sans",Arial,sans-serif;color:var(--ink);background:var(--white);position:relative}
a{color:inherit;text-decoration:none}

/* top bar */
.topbar{height:52px;background:var(--black);color:var(--white);display:flex;align-items:center;padding:0 40px;font-size:15px;position:relative}
.topbar .social{display:flex;gap:14px}
.topbar .social span{width:20px;height:20px;border:2px solid var(--white);border-radius:4px;display:block}
.topbar .promo{position:absolute;left:0;right:0;text-align:center;letter-spacing:.5px;pointer-events:none}
.topbar .locale{margin-left:auto;display:flex;gap:40px;font-size:14px}

/* header */
.header{height:88px;background:var(--black);display:flex;align-items:center;padding:0 40px;border-top:1px solid #2a2a2a}
.brand{display:flex;align-items:center;gap:10px;color:var(--white);font-family:"Raleway",sans-serif;font-weight:700;font-size:30px;letter-spacing:1px}
.brand .mark{width:22px;height:22px;background:var(--green);display:block}
.search{margin-left:125px;width:448px;height:46px;border:2px solid var(--white);display:flex;align-items:center;padding:0 14px;color:var(--white);font-size:16px}
.search svg{margin-left:auto}
.header-icons{margin-left:auto;display:flex;gap:22px;align-items:center}
.header-icons svg{display:block}

/* nav */
.nav{height:60px;display:flex;align-items:center;background:var(--white);box-shadow:0 2px 4px rgba(0,0,0,.08);position:relative;z-index:2}
.nav .categories{margin-left:40px;width:272px;height:60px;background:var(--green);color:var(--white);display:flex;align-items:center;padding:0 26px;font-family:"Raleway",sans-serif;font-weight:600;font-size:20px;letter-spacing:1px;gap:16px}
.nav ul{list-style:none;display:flex;gap:26px;margin-left:34px;font-family:"Raleway",sans-serif;font-size:16px;font-weight:600;color:var(--ink)}
.nav li.active{color:var(--green);border-bottom:2px solid var(--green)}

/* hero */
.hero{height:580px;position:relative;color:var(--white);text-align:center}
.hero .photo{position:absolute;inset:0;background:linear-gradient(100deg,#6f5a3d 0%,#a58455 35%,#c9a46f 55%,#7c8a66 80%,#5e6e4d 100%)}
.hero .shade{position:absolute;inset:0;background:rgba(0,0,0,.18)}
.hero .content{position:relative;padding-top:148px}
.hero h1{font-family:"Raleway",sans-serif;font-weight:500;font-size:64px;letter-spacing:2px}
.hero p{width:720px;margin:12px auto 0;font-size:21px;line-height:1.45}
.btn{display:inline-block;background:var(--green);color:var(--white);font-family:"Raleway",sans-serif;font-weight:600;font-size:20px;letter-spacing:.5px;padding:14px 26px}
.hero .btn{margin-top:34px}

/* latest products */
.latest{height:708px;padding-top:118px}
.section-title{text-align:center;font-family:"Raleway",sans-serif;font-weight:400;font-size:50px;letter-spacing:2px;color:var(--ink)}
.cards{display:flex;gap:16px;justify-content:center;margin-top:86px}
.card{width:332px;height:400px;border:2px solid var(--line);background:var(--white);padding:14px;text-align:center}
.card.featured{background:#f4f4f4;box-shadow:0 6px 18px rgba(0,0,0,.18)}
.card .thumb{height:206px;border-radius:4px}
.thumb.tools{background:radial-gradient(circle at 50% 50%,#6a6a6a 0%,#2b2b2b 40%,#eaeaea 42%,#f5f5f5 100%)}
.thumb.nut{background:radial-gradient(circle at 50% 50%,#dcdcdc 0%,#a9a9a9 35%,#e2e2e2 38%,#ececec 100%)}
.thumb.rivet{background:radial-gradient(ellipse at 50% 50%,#b8b8b8 0%,#8e8e8e 30%,#eeeeee 33%,#f8f8f8 100%)}
.card h3{margin-top:34px;font-family:"Raleway",sans-serif;font-weight:500;font-size:24px;letter-spacing:.5px}
.card p{margin:10px auto 0;width:260px;font-size:13px;line-height:1.4;color:var(--muted)}
.card .more{display:inline-block;margin-top:18px;font-size:16px;color:var(--green-dark);border-bottom:2px solid var(--green);letter-spacing:.5px}

/* welcome */
.welcome{height:372px;background:var(--soft);text-align:center;padding-top:44px}
.welcome .section-title{font-size:48px}
.welcome p{width:900px;margin:24px auto 0;font-size:19px;line-height:1.55;color:#333}
.welcome .btn{margin-top:30px;padding:12px 40px}

/* newsletter */
.newsletter{height:312px;text-align:center;padding-top:84px}
.newsletter .section-title{font-size:46px}
.signup{display:flex;justify-content:center;gap:44px;margin-top:40px}
.signup .field{width:548px;height:72px;border:2px solid #555;display:flex;align-items:center;padding:0 18px;gap:26px;font-size:18px;color:var(--muted)}
.signup .btn{width:246px;height:72px;display:flex;align-items:center;justify-content:center;font-size:22px;letter-spacing:1px}

/* footer */
.footer{position:absolute;left:0;top:2172px;width:1200px;height:420px;background:var(--black);color:var(--white)}
.footer .brand{position:absolute;left:140px;top:112px;font-size:32px}
.footer .col{position:absolute;top:56px}
.footer h4{font-family:"Raleway",sans-serif;font-weight:500;font-size:24px;letter-spacing:1px;margin-bottom:22px}
.footer ul{list-style:none;font-size:15px;line-height:27px}
.col.quick{left:382px}
.col.useful{left:630px}
.col.contact{left:930px}
.footer .bottom{position:absolute;left:0;right:0;bottom:0;height:64px;display:flex;align-items:center;padding:0 88px;font-size:15px}
.payments{margin-left:auto;display:flex;gap:12px}
.payments span{width:42px;height:26px;background:#d9d9d9;border-radius:3px;display:block}
</style>
</head>
<body>

<div class="topbar">
  <div class="social"><span></span><span></span></div>
  <div class="promo">FREE SHIPPING ON ALL ORDERS OVER $75</div>
  <div class="locale"><span>$ US</span><span>ENGLISH</span></div>
</div>

<header class="header">
  <div class="brand"><span class="mark"></span>K7M3</div>
  <div class="search">Product Search
    <svg width="22" height="22" viewBox="0 0 24 24" fill="none" stroke="#fff" stroke-width="2.5"><circle cx="10" cy="10" r="7"/><line x1="15.5" y1="15.5" x2="22" y2="22"/></svg>
  </div>
  <div class="header-icons">
    <svg width="22" height="22" viewBox="0 0 24 24" fill="none" stroke="#fff" stroke-width="2"><circle cx="12" cy="12" r="8"/><line x1="12" y1="7" x2="12" y2="17"/><line x1="7" y1="12" x2="17" y2="12"/></svg>
    <svg width="22" height="22" viewBox="0 0 24 24" fill="none" stroke="#fff" stroke-width="2"><circle cx="12" cy="8" r="4"/><path d="M4 22c0-5 4-8 8-8s8 3 8 8"/></svg>
    <svg width="24" height="22" viewBox="0 0 24 22" fill="none" stroke="#fff" stroke-width="2"><path d="M12 20S2 13 2 7a5 5 0 0 1 10-1 5 5 0 0 1 10 1c0 6-10 13-10 13z"/></svg>
    <svg width="24" height="22" viewBox="0 0 24 22" fill="none" stroke="#fff" stroke-width="2"><path d="M1 2h4l3 12h12l3-9H7"/><circle cx="10" cy="19" r="1.6"/><circle cx="18" cy="19" r="1.6"/></svg>
  </div>
</header>

<nav class="nav">
  <div class="categories">
    <svg width="20" height="16" viewBox="0 0 20 16" fill="#fff"><rect width="20" height="2.5"/><rect y="6.7" width="20" height="2.5"/><rect y="13.5" width="20" height="2.5"/></svg>
    CATEGORIES
  </div>
  <ul>
    <li class="active">HOME</li><li>MARIN</li><li>SCREW</li><li>STICKS</li><li>NUTS</li><li>TRAYS</li><li>SCREW PIN</li><li>CONTACT US</li><li>ABOUT US</li><li>MORE ⌄</li>
  </ul>
</nav>

<section class="hero">
  <div class="photo" role="img" aria-label="Worker in a blue cap fastening a wooden fence with a riveting tool"></div>
  <div class="shade"></div>
  <div class="content">
    <h1>BLIND RIVET</h1>
    <p>K7M3 sells stainless steel fasteners to stores, retailers and industry. On our site you can find most known bits and ISO standards in mounting.</p>
    <a class="btn" href="#">OTHER ATTACHMENT</a>
  </div>
</section>

<section class="latest">
  <h2 class="section-title">LATEST PRODUCTS</h2>
  <div class="cards">
    <article class="card">
      <div class="thumb tools" role="img" aria-label="Cordless riveting tool"></div>
      <h3>RIVETING TOOLS</h3>
      <p>Battery and manual riveting tools for fast and clean setting in production.</p>
      <a class="more" href="#">MORE INFORMATION</a>
    </article>
    <article class="card featured">
      <div class="thumb nut" role="img" aria-label="Stainless steel blind rivet nut"></div>
      <h3>BLIND RIVET NUT</h3>
      <p>Threaded blind rivet nuts in stainless steel for thin and soft sheet.</p>
      <a class="more" href="#">MORE INFORMATION</a>
    </article>
    <article class="card">
      <div class="thumb rivet" role="img" aria-label="Blind rivet with mandrel"></div>
      <h3>BLIND RIVETS</h3>
      <p>Open and closed end blind rivets in stainless steel and aluminium sizes.</p>
      <a class="more" href="#">MORE INFORMATION</a>
    </article>
  </div>
</section>

<section class="welcome">
  <h2 class="section-title">WELCOME TO BLIND RIVET</h2>
  <p>K7M3 AB is a wholesale company that caters to other companies. Our range consists of stainless steel products for mounting and marine applications. We have the widest and deepest range of stainless steel on the market. Our attachments comply with DIN standards and ISO standards.Prices shown on our website are gross prices, to get prices that apply to your business please contact us.</p>
  <a class="btn" href="#">READ MORE</a>
</section>

<section class="newsletter">
  <h2 class="section-title">NEWSLETTER &nbsp;SIGNUP</h2>
  <div class="signup">
    <div class="field">
      <svg width="26" height="20" viewBox="0 0 26 20" fill="none" stroke="#333" stroke-width="2"><rect x="1" y="1" width="24" height="18"/><path d="M1 1l12 10L25 1"/></svg>
      Enter your email address
    </div>
    <a class="btn" href="#">SUBSCRIBE</a>
  </div>
</section>

<footer class="footer">
  <div class="brand"><span class="mark"></span>K7M3</div>
  <div class="col quick">
    <h4>QUICKS LINKS</h4>
    <ul><li>Marin</li><li>Screw</li><li>Sticks</li><li>Nuts</li><li>Trays</li><li>Screw Pin</li><li>Contact Us</li><li>About Us</li></ul>
  </div>
  <div class="col useful">
    <h4>USEFUL LINKS</h4>
    <ul><li>Map to our store</li><li>Contact Us</li><li>International Shipping Info</li><li>Privacy &amp; Security</li><li>Satisfaction Guarantee</li></ul>
  </div>
  <div class="col contact">
    <h4>CONTACT US</h4>
    <ul><li>c / o Lindgården,</li><li>Norrvägen 9</li><li>431 22 Ekhamn</li><li>Tel: 0340-55 21 09</li><li>info@k7m3.se</li></ul>
  </div>
  <div class="bottom">
    <span>Copyright © 2020 &nbsp;Blind Rivet All Rights Reserved</span>
    <div class="payments"><span></span><span></span><span></span><span></span><span></span><span></span></div>
  </div>
</footer>

</body>
</html>
```